Call Center In Need of Website Design

We are a call center that provides inbound and outbound calling & marketing services for eCommerce store. We would like to see a fun, creative, playful design that is simple.

Here are some sample design sites we like;
- https://www.velmoreline.com/
- https://pindrask.io/
- https://www.glimbertic.com/live-chat-software/
- https://www.zavrolin.com/

Here are some competitor sites;
- https://www.ostrevaglinks.com/
- https://www.helpkestrel.com/

I have attached website content for your use.

Target Market(s)

eCommerce

Coding

Coded - Design and coding required

Number of Pages Required

5+ page

Font styles to use
Sans Serif

Colors

Designer to choose colors to be used in the design.

Requirements
Must have
• Must have designs for the following 5 separate pages;
• 1. Home (landing)
• - This will be were the design style really needs to show.
• - Just needs to touch on key services
• - CTA
• 2. About Us
• - Basic page for about me paragraph
• 3. Services
• - List of services with icons
• - Click on service type to expand details or hover over service icon to view popup bubble with details about that service
• 4. Pricing
• - Option to bundle 1(one) digital service plan and 1(one) call center service plan
• - Bundling adds 10% monthly discount to over all price
• - Customer does NOT have to bundle
• - FAQ
• 5. Contact Us
• - Include a capture form (name, company name, email, phone, message)
• - Contact info
• - Business hours
• When customer purchases their desired plan, then they are taken to a page where they must schedule a call with an account rep.
Nice to have
• home page animations
Should not have
• All information on Home/Landing page.

```html
<!DOCTYPE html>
<html lang="en">
<head>
<meta charset="utf-8">
<title>Orbitra — Omnichannel Customer Care</title>
<link rel="stylesheet" href="https://fonts.googleapis.com/css2?family=Poppins:wght@300;400;500;600;700&family=Montserrat:wght@300;400;600&display=swap">
<style>
:root{
  --blue:#1b3db2;
  --teal:#5fc4a8;
  --teal-light:#7dd0b9;
  --purple:#363a86;
  --purple-card:#3a3f90;
  --lavender:#a9acd8;
  --ink:#4a4a4a;
  --muted:#6b6b6b;
  --footer-teal:#67c3ab;
  --footer-dark:#1c1c1c;
  --white:#ffffff;
}
*{box-sizing:border-box;margin:0;padding:0}
html,body{width:827px;height:1200px;overflow:hidden}
body{font-family:"Montserrat",sans-serif;background:var(--white);position:relative;color:var(--ink)}
.abs{position:absolute}

/* hero */
.hero{left:0;top:0;width:827px;height:385px;overflow:hidden;
  background:linear-gradient(115deg,var(--blue) 0%,#2e63b8 35%,#4fa4b3 62%,var(--teal) 85%)}
.bubble{position:absolute;border-radius:50%}
.brand{left:110px;top:28px;display:flex;align-items:center;gap:12px;
  font-family:"Poppins",sans-serif;font-weight:300;font-size:27px;letter-spacing:5px;color:var(--white)}
.brand-dot{width:34px;height:34px;border:2px solid var(--teal-light);border-radius:50%}
.nav{left:389px;top:42px;display:flex;gap:25px;font-family:"Poppins",sans-serif;font-size:7px;font-weight:500;letter-spacing:.5px;color:rgba(255,255,255,.8)}
.nav .active{color:var(--white);font-weight:600}
.hero-title{left:0;top:155px;width:827px;text-align:center;font-family:"Poppins",sans-serif;color:var(--white)}
.hero-title .l1{font-size:29px;font-weight:600;line-height:36px}
.hero-title .l2{font-size:28px;font-weight:300;line-height:36px}
.hero-btns{left:341px;top:247px;display:flex;gap:6px}
.btn{width:70px;height:25px;border:1.5px solid var(--white);display:flex;align-items:center;justify-content:center;
  font-family:"Poppins",sans-serif;font-size:7px;font-weight:600;color:var(--white)}

/* about band */
.about{left:0;top:385px;width:827px;height:353px;background:var(--purple)}
.about-divider{left:0;top:541px;width:827px;height:1px;background:rgba(255,255,255,.08)}
.section-title{font-family:"Poppins",sans-serif;font-weight:600;font-size:18px}
.wordmark{font-family:"Poppins",sans-serif;font-weight:300;font-size:25px;letter-spacing:6px}
.about .section-title{left:111px;top:42px;color:var(--white)}
.about .wordmark{left:111px;top:92px;color:var(--white)}
.about-text{left:413px;top:43px;width:306px;font-size:6.6px;line-height:14.4px;color:var(--lavender)}

/* service cards */
.card{top:157px;width:228px;height:196px;background:linear-gradient(180deg,var(--purple) 0%,var(--purple-card) 100%)}
.card-head{left:25px;top:24px;display:flex;align-items:center;gap:10px;font-family:"Poppins",sans-serif;font-weight:500;font-size:13.5px;color:var(--white)}
.card-list{left:25px;top:72px;list-style:none;font-size:7px;line-height:10.8px;color:var(--lavender)}
.card-list li::before{content:"o";display:inline-block;width:18px}
.card-link{left:25px;top:157px;font-family:"Poppins",sans-serif;font-size:7px;font-weight:600;color:var(--white)}

/* faq & intro */
.lower{left:0;top:738px;width:827px;height:383px;background:linear-gradient(180deg,#ffffff 0%,#f6f6f6 100%)}
.curve{left:0;top:738px}
.faq-title{left:111px;top:68px;color:var(--teal)}
.lower .wordmark{left:111px;top:120px;color:#444}
.faq-q{left:383px;top:72px;font-family:"Poppins",sans-serif;font-size:7px;font-weight:600;color:#333}
.faq-a{left:383px;top:85px;width:335px;font-size:6.6px;line-height:14.4px;color:var(--muted)}
.rule{left:111px;top:172px;width:605px;height:1px;background:#e2e2e2}
.illustration{left:110px;top:200px;width:220px;height:150px;border-radius:60px 80px 20px 20px;
  background:radial-gradient(circle at 60% 45%,#f06060 0%,#e6807a 25%,#8fd3bd 55%,#e9f3ef 100%)}
.intro{left:376px;top:217px;width:345px;font-size:6.6px;line-height:14.4px;color:var(--muted)}
.intro p+p{margin-top:14.4px}

/* footer */
.footer{left:0;top:1121px;width:827px;height:45px;background:var(--footer-teal);color:var(--white);font-size:7px}
.f-item{top:18px;display:flex;align-items:center;gap:5px}
.f-nav{left:463px;top:18px;display:flex;gap:17px;font-family:"Poppins",sans-serif;font-weight:600}
.copyright{left:0;top:1166px;width:827px;height:34px;background:var(--footer-dark);color:var(--white);
  font-size:6.6px;display:flex;align-items:center;justify-content:center}
</style>
</head>
<body>

<header class="hero abs">
  <div class="bubble" style="left:120px;top:70px;width:270px;height:270px;background:rgba(70,130,200,.45)"></div>
  <div class="bubble" style="left:300px;top:-60px;width:160px;height:160px;background:rgba(80,140,210,.35)"></div>
  <div class="bubble" style="left:92px;top:300px;width:142px;height:142px;background:linear-gradient(180deg,rgba(60,120,200,.6),rgba(95,196,168,.4))"></div>
  <div class="bubble" style="left:278px;top:300px;width:140px;height:140px;background:linear-gradient(180deg,rgba(60,120,200,.6),rgba(95,196,168,.4))"></div>
  <div class="bubble" style="left:570px;top:245px;width:340px;height:340px;background:rgba(140,215,195,.45)"></div>

  <div class="brand abs"><span class="brand-dot"></span>ORBITRA</div>
  <nav class="nav abs">
    <span class="active">HOME</span><span>ABOUT US</span><span>SERVICES</span><span>PRICING</span><span>CONTACT US</span><span>ACCOUNT</span>
  </nav>
  <h1 class="hero-title abs"><span class="l1">Orbitra Is An Omnichannel</span><br><span class="l2">Provider For Customer Care</span></h1>
  <div class="hero-btns abs"><span class="btn">Learn More</span><span class="btn">Plans &amp; Pricing</span></div>
</header>

<section class="about abs">
  <h2 class="section-title abs">What Orbitra Do</h2>
  <div class="wordmark abs">ORBITRA</div>
  <p class="about-text abs">Orbitra is your personal customer service and product research team. We love eCommerce, but we love seeing business owners succeed even more! That is exactly why we have developed the processes and technology to take care of the most over looked areas in eCommerce - Customer Service and Retention.<br>Let Orbitra handle your customers while you focus on growing your business.</p>

  <article class="card abs" style="left:190px">
    <div class="card-head abs">
      <svg width="35" height="30" viewBox="0 0 35 30" fill="none" stroke="#fff" stroke-width="1.6"><rect x="3" y="3" width="29" height="19" rx="1"/><path d="M0 26h35"/><circle cx="17" cy="11" r="4"/><path d="M17 5v2M17 15v2M11 11h2M21 11h2"/></svg>
      Digital Services
    </div>
    <ul class="card-list abs">
      <li>Email Support</li><li>Live Chat Support</li><li>Product Research</li><li>Product Listing</li><li>Price Monitoring</li><li>Product Photo &amp; Video Editing</li>
    </ul>
    <span class="card-link abs">Learn More</span>
  </article>

  <article class="card abs" style="left:438px">
    <div class="card-head abs">
      <svg width="33" height="32" viewBox="0 0 33 32" fill="none" stroke="#fff" stroke-width="1.8"><circle cx="16" cy="12" r="9"/><path d="M5 14v-3M27 14v-3M24 20q-3 3-8 3"/><path d="M2 31q2-6 14-6t14 6"/></svg>
      Call Center Services
    </div>
    <ul class="card-list abs">
      <li>Answering service</li><li>Welcome Calls</li><li>Follow-Up Service</li><li>Customer Upselling</li><li>Over-The-Phone Order Taking</li><li>Order Return Processing</li>
    </ul>
    <span class="card-link abs">Learn More</span>
  </article>
</section>
<div class="about-divider abs"></div>

<section class="lower abs">
  <h2 class="section-title faq-title abs">Frequently Asked Quetions</h2>
  <div class="wordmark abs">ORBITRA</div>
  <h3 class="faq-q abs">Is the free trial really free?</h3>
  <p class="faq-a abs">The free trial only relates to the “call center” service packages! There is no hidden fine print or fees to get started. We don’t even require any payment info, signatures, or deposits. If you don’t like us or our service, just simply walk away.</p>
  <div class="rule abs"></div>
  <div class="illustration abs" role="img" aria-label="Illustration of a laptop, tablet and phone showing chat bubbles over a teal globe"></div>
  <div class="intro abs">
    <p>Orbitra is an omnichannel provider for customer care and back-end office support. We primarily work with eCommerce companies around the world. Our service is vital to the core operations and functionality of consumer-focused online eCommerce companies.</p>
    <p>Orbitra originally started out as a generalized call center support company. Based in California, the founder quickly realized that there was a lack of support for eCommerce owners that were just getting started. In 2018, Orbitra switched gears to offer professional grade call center support at a price that even start-ups could afford.</p>
  </div>
</section>
<svg class="curve abs" width="220" height="120" viewBox="0 0 220 120"><path d="M0 0H220Q60 0 0 120Z" fill="#363a86"/></svg>

<footer class="footer abs">
  <div class="f-item abs" style="left:111px">
    <svg width="8" height="11" viewBox="0 0 8 11"><path d="M4 0a4 4 0 0 1 4 4c0 3-4 7-4 7S0 7 0 4a4 4 0 0 1 4-4z" fill="#fff"/><circle cx="4" cy="4" r="1.5" fill="#67c3ab"/></svg>
    418 Larkhaven Ave. Fresno, CA 93720
  </div>
  <div class="f-item abs" style="left:274px">
    <svg width="10" height="7" viewBox="0 0 10 7" fill="none" stroke="#fff"><rect x=".5" y=".5" width="9" height="6"/><path d="M.5 .5 5 4l4.5-3.5"/></svg>
    hello@orbitra.inc
  </div>
  <div class="f-item abs" style="left:374px">
    <svg width="8" height="9" viewBox="0 0 8 9" fill="none" stroke="#fff" stroke-width="1.2"><path d="M2 1Q0 4 2 8M2 1l2 1-1 2M2 8l2-1-1-2"/></svg>
    (800) 555-0147
  </div>
  <nav class="f-nav abs"><span>Home</span><span>About</span><span>Services</span><span>Pricing</span><span>Contact Us</span><span>Account</span></nav>
</footer>
<div class="copyright abs">Copyright © 2018 Orbitra. All Rights Reserved.</div>

</body>
</html>
```